Las Vegas transportation company needs a dynamic design for business cards

We are a transportation management company based in Las Vegas specializing in operating and maintaining public transit systems. We want to keep our existing logo but would like to design business cards that feature one or more transit systems (e.g. monorail, train, bus) and maybe also the Las Vegas landscape.

```html
<!DOCTYPE html>
<html lang="en">
<head>
<meta charset="UTF-8">
<title>Meridian Transit Group – Business Cards</title>
<link rel="stylesheet" href="https://fonts.googleapis.com/css2?family=Cinzel:wght@500;600&family=Lato:wght@400;700&display=swap">
<style>
  :root {
    --navy: #0d1f66;
    --sky: #8ab8e8;
    --ink: #1c1c24;
    --paper: #ffffff;
    --stage: #e9e7e3;
    --scene-sky: #d6dfea;
    --scene-ridge: #e8ecf1;
    --scene-snow: #f6f7f9;
  }
  * { box-sizing: border-box; margin: 0; padding: 0; }
  html, body {
    width: 1200px; height: 900px; overflow: hidden;
    background: var(--stage);
  }
  .canvas { position: relative; width: 1200px; height: 900px; }
  .card {
    position: absolute; left: 280px; width: 640px; height: 366px;
    background: var(--paper);
    box-shadow: 0 4px 14px rgba(0,0,0,0.18);
    overflow: hidden;
  }
  .card--front { top: 60px; }
  .card--back { top: 470px; }

  /* Front */
  .front-scene {
    position: absolute; inset: 0;
    background: linear-gradient(180deg, var(--scene-sky) 0%, var(--scene-ridge) 30%, var(--scene-snow) 62%, var(--paper) 100%);
  }
  .brand {
    position: absolute; left: 0; right: 0; top: 150px;
    display: flex; align-items: center; justify-content: center; gap: 14px;
    font-family: "Cinzel", serif; font-weight: 600;
    color: var(--navy);
  }
  .brand__mark { width: 26px; height: 26px; background: var(--navy); flex: none; }
  .brand__name { font-size: 34px; letter-spacing: 2px; line-height: 1; white-space: nowrap; }

  /* Back */
  .wave { position: absolute; inset: 0; }
  .vehicle-photo {
    position: absolute; left: 400px; top: 40px; width: 215px; height: 140px;
    border-radius: 30px 14px 12px 34px;
    background: linear-gradient(160deg, #5c86d6 0%, #2748b0 55%, #1a2f80 100%);
  }
  .person { position: absolute; left: 46px; top: 70px; color: var(--navy); }
  .person__name {
    font-family: "Cinzel", serif; font-weight: 600;
    font-size: 30px; letter-spacing: 1.5px; line-height: 1;
  }
  .person__title {
    font-family: "Lato", sans-serif; font-size: 16px;
    color: var(--ink); margin-top: 4px; letter-spacing: 0.3px;
  }
  .contact {
    position: absolute; left: 62px; top: 150px;
    font-family: "Lato", sans-serif; font-size: 17px; color: var(--ink);
    list-style: none; letter-spacing: 0.4px;
  }
  .contact__line { display: flex; align-items: center; gap: 10px; height: 26px; }
  .contact__icon { width: 20px; height: 18px; fill: var(--navy); flex: none; }
  .address {
    position: absolute; left: 62px; top: 212px;
    font-family: "Lato", sans-serif; font-size: 17px; line-height: 25px;
    color: var(--ink); font-style: normal; letter-spacing: 0.4px;
  }
  .website {
    position: absolute; right: 36px; bottom: 34px;
    font-family: "Lato", sans-serif; font-size: 15px; color: var(--paper);
    letter-spacing: 0.5px;
  }
</style>
</head>
<body>
<main class="canvas">

  <section class="card card--front" aria-label="Business card front">
    <div class="front-scene" role="img" aria-label="Faded full-bleed photograph of a red passenger train travelling through a snowy mountain valley under a pale sky"></div>
    <div class="brand">
      <span class="brand__mark"></span>
      <span class="brand__name">MERIDIAN TRANSIT GROUP</span>
    </div>
  </section>

  <section class="card card--back" aria-label="Business card back">
    <svg class="wave" viewBox="0 0 640 366" preserveAspectRatio="none" aria-hidden="true">
      <path d="M0,298 C210,300 360,262 640,150 L640,366 L0,366 Z" fill="var(--navy)"/>
      <path d="M0,278 C200,288 340,262 500,206 C370,268 210,296 0,296 Z" fill="var(--sky)"/>
    </svg>

    <div class="vehicle-photo" role="img" aria-label="Photograph of a blue intercity coach bus"></div>

    <div class="person">
      <h1 class="person__name">DANIEL REYES</h1>
      <p class="person__title">Managing Director</p>
    </div>

    <ul class="contact">
      <li class="contact__line">
        <svg class="contact__icon" viewBox="0 0 24 24" aria-hidden="true">
          <path d="M6.6 10.8a15.2 15.2 0 0 0 6.6 6.6l2.2-2.2c.3-.3.7-.4 1-.2 1.1.4 2.3.6 3.6.6.6 0 1 .4 1 1V20c0 .6-.4 1-1 1C10.6 21 3 13.4 3 4c0-.6.4-1 1-1h3.5c.6 0 1 .4 1 1 0 1.3.2 2.5.6 3.6.1.3 0 .7-.2 1z"/>
        </svg>
        <span>044-555 018 240</span>
      </li>
      <li class="contact__line">
        <svg class="contact__icon" viewBox="0 0 24 18" aria-hidden="true">
          <path d="M1 1h22v16H1z M3 3v1l9 6 9-6V3z" fill-rule="evenodd"/>
        </svg>
        <span>info@meridian.com</span>
      </li>
    </ul>

    <address class="address">
      88, Depot Avenue East<br>
      Summit Valley, 45120
    </address>

    <p class="website">www.meridiantransit.com</p>
  </section>

</main>
</body>
</html>
```